Lotstallmart.com Webpage Design

Design Brief for lotstallmart.com (Copy of Brief also in attached Word file)

Name of Website- lotstallmart.com (existing logo and look & feel of website to be changed)

Logo - Finalised. The logo files are attached with the brief as “logo.jpeg”. The “Blue- Grey” version of the logo is for use on lighter backgrounds and the “Orange-White” version of the logo is for use on darker backgrounds. (A full Black version of the logo is also attached). Both versions may be used in different parts of the website. All attached files are in .png format.
Status - The website in functional and is undergoing user trials. However, we want to improve the look & feel of the website so at it seems
a. cotemporary,
b. Easy to Navigate
c. professional and
d. Vibrant.

Please visit ‘lotstallmart.com’ to check out the website and its functionalities – please use it only as a reference for the features & functions to be provided, however the designer should use a ‘Free Hand’ in designing the composition of various parts of the webpage without getting too influenced by the existing design

Objective of the Website ‘lotstallmart.com –
a. It is a portal focussed on listing of ‘Retail’ specific real-estate properties by developers, owners and realty brokers. The properties shall listed under the following four categories-
i. Retail Malls
ii. Shopping Complexes
iii. High-street shops
iv. Retail Warehouses
*refer lotstallmart.com for better clarity

b. The abovementioned properties shall be listed either for ‘Sale’ or ‘rent\lease’ or both

c. Users shall visit the site in case they wish to acquire a retail \ shop space either on ‘sale’ or ‘rent’. These Users would be able to specify the ‘Search Criteria’ through the tool-bars provided on the website – the ‘Search Criteria’ shall comprise of ‘Type of space category’, ‘City’, ‘Locality’, transaction type ie ‘Rent \ Sale’ and ‘Area Range’

d. The main revenue model for the website shall be listing fee ( or advertising charges ) payable by those listing their properties on the website.

Three Main Pages of Website (lotstallmart.com) that need to be designed -
a. Main Home Page (visit the web link - http://lotstallmart.com/ ) - The main home page has the “Search Toolbar” for specifying of Search Criteria by the User. It shall also have the following features & functions-
i. Main Advertising Banner
ii. Featured Projects
iii. New Launches
iv. Toolbar with buttons – ‘Advertise with Us’, ‘Listings Alert’, ‘Mart Wizards’, ‘Advertiser Login’

b. Property Listings Page (visit the web link - http://lotstallmart.com/gurgaon-in-india ) - The List of property options that match the Criteria specified by the ‘User’ get displayed on this page.

c. Property Detail Page - When the ‘User’ clicks on the “More….” Button on the ‘Property Listings Page’ (given in point b. above) the web page with the details of the property opens. (For Example – visit the web link - http://lotstallmart.com/vorne-Shopping-Complex-vorne-quadrion-gurgaon-636 )

Note:- Please refer to attached ‘Shopping’ related images the designer may use them on the website to provide a look & feel of retail if required – either separately or rotate in a single window

Target Market(s)

Retailers & Investors looking for retail space, Real Estate Brokers, Developers

Industry/Entity Type

Advertising

Number of Pages Required

3 page

Requirements
Must have
• Refer to existing site lotstallmart.com -- all the existing functionalities are a must have.
Nice to have
• The Designer may use the retail related images on the website if required for making it more vibrant. Refer attached images Shopping(1-6).jpg

```html
<!DOCTYPE html>
<html lang="en">
<head>
<meta charset="utf-8">
<title>Lotstallmart.com – Portal for Retail Space</title>
<link rel="stylesheet" href="https://fonts.googleapis.com/css2?family=Open+Sans:wght@400;600;700;800&display=swap">
<style>
:root{
  --blue:#1b75bb;
  --blue-light:#3a9ad9;
  --navy:#0e3a60;
  --orange:#f7931e;
  --orange-dark:#e07f0c;
  --page-bg:#eceff2;
  --card-bg:#ffffff;
  --text:#333a40;
  --muted:#8a9299;
  --line:#d7dce0;
  --footer:#2c2f33;
  --footer-deep:#1f2124;
  --white:#ffffff;
}
*{box-sizing:border-box;margin:0;padding:0}
html,body{width:1200px;height:2580px;overflow:hidden}
body{font-family:"Open Sans",Arial,sans-serif;color:var(--text);background:var(--page-bg);font-size:12px}
.page{position:relative;width:1200px;height:2580px;overflow:hidden;background:var(--page-bg)}

/* header */
.site-header{position:absolute;left:0;top:0;width:1200px;height:96px;background:var(--white)}
.brand{position:absolute;left:28px;top:24px;display:flex;align-items:center;gap:10px}
.brand-dot{width:34px;height:34px;border-radius:50%;background:var(--blue)}
.brand-name{font-size:28px;font-weight:700;color:var(--blue);letter-spacing:-.5px}
.city-nav{position:absolute;left:330px;top:0;width:870px;height:28px;background:var(--navy);display:flex;justify-content:space-around;align-items:center}
.city-nav a{color:#cfe0ee;text-decoration:none;font-size:11px}
.utility-nav{position:absolute;left:440px;top:38px;display:flex;gap:46px}
.utility-item strong{display:block;font-size:10px;font-weight:700;color:var(--navy);letter-spacing:.4px}
.utility-item span{display:block;font-size:10px;color:var(--muted);margin-top:2px}
.header-actions{position:absolute;right:16px;top:34px;width:190px}
.btn-header{display:block;height:26px;line-height:26px;color:var(--white);font-size:10px;font-weight:700;padding-left:12px;margin-bottom:4px;letter-spacing:.3px}
.btn-header.orange{background:var(--orange)}
.btn-header.blue{background:var(--blue)}

/* hero */
.hero{position:absolute;left:0;top:96px;width:1200px;height:508px;background:linear-gradient(160deg,#6d5a46 0%,#a08466 35%,#5c6b78 70%,#34424e 100%)}
.hero-title{position:absolute;left:36px;top:380px;color:var(--white);font-size:38px;font-weight:800;line-height:1.15;letter-spacing:.5px;text-transform:uppercase}

/* sidebar */
.sidebar{position:absolute;left:992px;top:112px;width:192px}
.format-tile{height:140px;margin-bottom:8px;padding:16px;color:var(--white)}
.format-tile h3{font-size:12px;font-weight:700;letter-spacing:.4px}
.format-tile p{font-size:10px;line-height:1.5;margin-top:8px;opacity:.85}
.format-tile.blue{background:var(--blue)}
.format-tile.light{background:var(--blue-light)}
.format-tile.orange{background:var(--orange)}
.wizards-box{background:var(--orange);padding:16px;height:474px;margin-top:12px;color:var(--white)}
.wizards-box h3{font-size:12px;font-weight:700}
.wizards-box p{font-size:10px;line-height:1.5;margin:8px 0 14px}
.field{background:var(--white);height:28px;margin-bottom:8px;font-size:10px;color:var(--muted);line-height:28px;padding-left:8px}
.field.tall{height:90px}
.btn-send{display:block;width:70px;height:26px;margin:6px auto 0;background:var(--navy);color:var(--white);font-size:10px;font-weight:700;text-align:center;line-height:26px}
.side-panel{background:var(--white);padding:16px;margin-top:20px}
.side-panel h3{font-size:11px;font-weight:700;color:var(--navy)}
.side-panel p{font-size:10px;line-height:1.55;color:var(--muted);margin:8px 0}
.side-panel .field{border:1px solid var(--line);height:26px;line-height:24px}
.link-more{font-size:10px;color:var(--blue);font-weight:600}

/* search */
.search-panel{position:absolute;left:32px;top:608px;width:928px;height:212px;background:var(--white)}
.search-head{height:44px;background:var(--navy);color:var(--white);font-size:14px;font-weight:700;padding-left:18px;line-height:44px}
.search-head span{font-weight:400;font-size:12px;color:#9fc1dd}
.format-options{display:flex;gap:40px;padding:16px 18px 10px}
.format-options label{display:flex;align-items:center;gap:6px;font-size:11px;color:var(--text)}
.radio{width:11px;height:11px;border-radius:50%;border:1px solid var(--muted)}
.radio.on{border:3px solid var(--blue)}
.search-fields{position:relative;padding:4px 18px}
.select-row{display:flex;gap:12px;margin-bottom:10px}
.select{width:200px;height:30px;border:1px solid var(--line);font-size:10px;color:var(--muted);line-height:28px;padding-left:10px;position:relative}
.select::after{content:"";position:absolute;right:10px;top:12px;border:4px solid transparent;border-top-color:var(--muted)}
.btn-search{position:absolute;right:18px;top:4px;width:230px;height:70px;background:var(--orange);color:var(--white);font-size:15px;font-weight:700;display:flex;align-items:center;justify-content:center;gap:10px}

/* sections */
.section{position:absolute;left:32px;width:928px}
.section-head{height:40px;display:flex;align-items:center;justify-content:space-between;border-bottom:2px solid var(--line)}
.section-head h2{font-size:13px;font-weight:700;color:var(--navy);letter-spacing:.3px}
.section-head h2 small{font-size:9px;color:var(--muted);font-weight:400;margin-left:4px}
.pager{display:flex;gap:4px}
.pager span{width:18px;height:18px;background:var(--white);border:1px solid var(--line);display:flex;align-items:center;justify-content:center}
.card-grid{display:grid;grid-template-columns:repeat(5,176px);column-gap:12px;row-gap:14px;margin-top:12px}
.card{background:var(--card-bg);height:214px;border:1px solid var(--line)}
.card-photo{position:relative;height:110px}
.photo-a{background:linear-gradient(180deg,#8fb4d4,#52687b)}
.photo-b{background:linear-gradient(180deg,#a9c6de,#6f7f8c)}
.photo-c{background:linear-gradient(180deg,#3e4f6a,#1e2a3a)}
.card-city{position:absolute;left:0;bottom:0;background:rgba(0,0,0,.6);color:var(--white);font-size:9px;padding:3px 8px}
.card-body{padding:8px 10px;height:68px}
.card-body h4{font-size:11px;font-weight:700;color:var(--orange)}
.card-body p{font-size:10px;color:var(--muted);margin-top:3px}
.btn-view{display:block;margin:0 10px;height:26px;line-height:26px;text-align:center;font-size:10px;background:#e4e7ea;color:var(--text)}
.btn-view.active{background:var(--orange);color:var(--white)}

/* spotlight */
.spotlight{position:absolute;left:32px;top:1372px;width:928px;height:224px;background:var(--white);border:1px solid var(--line);padding:12px}
.spotlight-photo{position:absolute;left:12px;top:12px;width:268px;height:198px;background:linear-gradient(160deg,#9dc0dc,#4c6276)}
.spotlight-info{position:absolute;left:300px;top:18px;width:320px}
.spotlight-info dl{display:grid;grid-template-columns:90px 1fr;row-gap:8px;font-size:11px}
.spotlight-info dt{color:var(--blue);font-weight:700}
.spotlight-info dd{color:var(--text)}
.spotlight-info p{font-size:10px;color:var(--muted);line-height:1.55;margin-top:10px}
.spotlight-info p a{color:var(--blue)}

/* footer */
.site-footer{position:absolute;left:0;top:2290px;width:1200px;height:258px;background:var(--footer);color:#b5bbc1}
.footer-cols{display:flex;gap:40px;padding:28px 32px 0}
.footer-col{width:248px}
.footer-col h5{font-size:11px;font-weight:700;color:var(--white);letter-spacing:.4px;margin-bottom:12px}
.footer-col p,.footer-col li{font-size:10px;line-height:1.7;list-style:none}
.footer-links{display:grid;grid-template-columns:1fr 1fr;column-gap:10px}
.follow-list{display:grid;grid-template-columns:1fr 1fr;gap:10px}
.follow-list li{display:flex;align-items:center;gap:8px}
.follow-list i{width:18px;height:18px;background:#4a4f55;display:block}
.footer-brand{position:absolute;right:32px;bottom:18px;display:flex;align-items:center;gap:8px}
.footer-brand .brand-dot{width:24px;height:24px;background:var(--orange)}
.footer-brand span{font-size:20px;font-weight:700;color:var(--white)}
.copyright{position:absolute;left:0;top:2548px;width:1200px;height:32px;background:var(--footer-deep);color:#8d939a;font-size:10px;text-align:center;line-height:32px}
</style>
</head>
<body>
<div class="page">

  <header class="site-header">
    <div class="brand"><span class="brand-dot"></span><span class="brand-name">lotstallmart</span></div>
    <nav class="city-nav">
      <a>Bangalore</a><a>Chennai</a><a>Chandigarh</a><a>Gurgaon</a><a>Hyderabad</a><a>Jaipur</a><a>Kolkata</a><a>Mumbai</a><a>Noida</a><a>Pune</a><a>More</a>
    </nav>
    <div class="utility-nav">
      <div class="utility-item"><strong>ADVERTISE WITH US</strong><span>Standard listing · Plans</span></div>
      <div class="utility-item"><strong>MART WIZARDS</strong><span>Ask our retail experts</span></div>
      <div class="utility-item"><strong>LISTING ALERT</strong><span>Get new listings by mail</span></div>
    </div>
    <div class="header-actions">
      <a class="btn-header orange">ADVERTISER LOGIN</a>
      <a class="btn-header blue">NEW REGISTER LOGIN</a>
    </div>
  </header>

  <section class="hero" role="img" aria-label="Photo of shoppers carrying bags in a bright shopping mall">
    <h1 class="hero-title">India's Leading<br>Portal for Retail Space</h1>
  </section>

  <aside class="sidebar">
    <div class="format-tile blue"><h3>RETAIL MALLS</h3><p>Anchor and inline spaces in malls across India.</p></div>
    <div class="format-tile light"><h3>SHOPPING COMPLEXES</h3><p>Shops in planned complexes near homes.</p></div>
    <div class="format-tile blue"><h3>HIGH STREET SHOPS</h3><p>Frontage shops on busy market streets.</p></div>
    <div class="format-tile light"><h3>RETAIL WAREHOUSES</h3><p>Large-format stores and storage spaces.</p></div>

    <div class="wizards-box">
      <h3>MART WIZARDS</h3>
      <p>Share your need and our retail space experts will call you back with the best options.</p>
      <div class="field">Name</div>
      <div class="field">Your email address</div>
      <div class="field">Phone number</div>
      <div class="field">City</div>
      <div class="field tall">Describe your requirement</div>
      <a class="btn-send">SEND</a>
    </div>

    <div class="side-panel">
      <h3>LISTING ALERT</h3>
      <p>Subscribe to receive new listings that match your search.</p>
      <div class="field">Enter your email</div>
      <div class="field">Select city</div>
      <div class="field">Select format</div>
    </div>

    <div class="side-panel">
      <h3>WWW.LOTSTALLMART.COM</h3>
      <p>Lotstallmart.com is a portal dedicated to retail real estate, listing malls, complexes, high street shops and warehouses for sale or rent across Indian cities.</p>
      <p>Owners, developers and brokers can list spaces and reach serious retailers and investors.</p>
      <span class="link-more">[ Read More ]</span>
    </div>
  </aside>

  <section class="search-panel">
    <div class="search-head">SELECT RETAIL FORMAT: <span>MEANING OF RETAIL FORMAT</span></div>
    <div class="format-options">
      <label><span class="radio on"></span>Retail Malls</label>
      <label><span class="radio"></span>Shopping Complexes</label>
      <label><span class="radio"></span>High Street Shops</label>
      <label><span class="radio"></span>Retail Warehouses</label>
    </div>
    <div class="search-fields">
      <div class="select-row">
        <div class="select">Select City</div>
        <div class="select">Select Locality</div>
        <div class="select">Rent / Sale</div>
      </div>
      <div class="select-row">
        <div class="select">Min Area</div>
        <div class="select">Max Area</div>
        <div class="select">Area Unit</div>
      </div>
      <a class="btn-search">
        <svg width="20" height="20" viewBox="0 0 20 20"><circle cx="8" cy="8" r="6" fill="none" stroke="#fff" stroke-width="2.4"/><line x1="12.5" y1="12.5" x2="18" y2="18" stroke="#fff" stroke-width="2.6"/></svg>
        SEARCH NOW
      </a>
    </div>
  </section>

  <section class="section" style="top:840px">
    <div class="section-head">
      <h2>FEATURED RETAIL PROJECTS <small>ACROSS INDIA</small></h2>
      <div class="pager">
        <span><svg width="8" height="8" viewBox="0 0 8 8"><path d="M5.5 1 2.5 4l3 3" fill="none" stroke="#8a9299" stroke-width="1.5"/></svg></span>
        <span><svg width="8" height="8" viewBox="0 0 8 8"><path d="M2.5 1l3 3-3 3" fill="none" stroke="#8a9299" stroke-width="1.5"/></svg></span>
      </div>
    </div>
    <div class="card-grid">
      <article class="card"><div class="card-photo photo-a" role="img" aria-label="Photo of a retail building"><span class="card-city">Surat</span></div><div class="card-body"><h4>Orvane Plaza</h4><p>Shopping Complex</p></div><a class="btn-view active">View the listing</a></article>
      <article class="card"><div class="card-photo photo-b" role="img" aria-label="Photo of a mall facade"><span class="card-city">Faridabad</span></div><div class="card-body"><h4>Orvane Plaza</h4><p>Shopping Complex</p></div><a class="btn-view">View the listing</a></article>
      <article class="card"><div class="card-photo photo-a" role="img" aria-label="Photo of a commercial tower"><span class="card-city">Gurgaon</span></div><div class="card-body"><h4>Orvane Plaza</h4><p>Shopping Complex</p></div><a class="btn-view">View the listing</a></article>
      <article class="card"><div class="card-photo photo-c" role="img" aria-label="Photo of a mall lit at night"><span class="card-city">Noida</span></div><div class="card-body"><h4>Orvane Plaza</h4><p>Shopping Complex</p></div><a class="btn-view">View the listing</a></article>
      <article class="card"><div class="card-photo photo-b" role="img" aria-label="Photo of a glass office tower"><span class="card-city">Gurgaon</span></div><div class="card-body"><h4>Orvane Plaza</h4><p>Shopping Complex</p></div><a class="btn-view">View the listing</a></article>
      <article class="card"><div class="card-photo photo-b" role="img" aria-label="Photo of a retail building"><span class="card-city">Surat</span></div><div class="card-body"><h4>Orvane Plaza</h4><p>Shopping Complex</p></div><a class="btn-view">View the listing</a></article>
      <article class="card"><div class="card-photo photo-a" role="img" aria-label="Photo of a mall facade"><span class="card-city">Faridabad</span></div><div class="card-body"><h4>Orvane Plaza</h4><p>Shopping Complex</p></div><a class="btn-view">View the listing</a></article>
      <article class="card"><div class="card-photo photo-c" role="img" aria-label="Photo of a commercial block"><span class="card-city">Gurgaon</span></div><div class="card-body"><h4>Orvane Plaza</h4><p>Shopping Complex</p></div><a class="btn-view">View the listing</a></article>
      <article class="card"><div class="card-photo photo-a" role="img" aria-label="Photo of a shopping centre"><span class="card-city">Noida</span></div><div class="card-body"><h4>Orvane Plaza</h4><p>Shopping Complex</p></div><a class="btn-view">View the listing</a></article>
      <article class="card"><div class="card-photo photo-b" role="img" aria-label="Photo of a retail tower"><span class="card-city">Gurgaon</span></div><div class="card-body"><h4>Orvane Plaza</h4><p>Shopping Complex</p></div><a class="btn-view">View the listing</a></article>
    </div>
  </section>

  <section class="spotlight">
    <div class="spotlight-photo" role="img" aria-label="Photo of a modern retail complex with glass front"></div>
    <div class="spotlight-info">
      <dl>
        <dt>Name</dt><dd>Kestrel Central</dd>
        <dt>City</dt><dd>Gurgaon</dd>
        <dt>Locality</dt><dd>Sector 66, Gurgaon</dd>
        <dt>Retail Format</dt><dd>Shopping Complex</dd>
      </dl>
      <p>A well connected retail destination with double height shop fronts, ample parking and a food court planned for high daily footfall. <a>[ Read More ]</a></p>
    </div>
  </section>

  <section class="section" style="top:1620px">
    <div class="section-head">
      <h2>FEATURED NEW LAUNCHES <small>ACROSS INDIA</small></h2>
      <div class="pager">
        <span><svg width="8" height="8" viewBox="0 0 8 8"><path d="M5.5 1 2.5 4l3 3" fill="none" stroke="#8a9299" stroke-width="1.5"/></svg></span>
        <span><svg width="8" height="8" viewBox="0 0 8 8"><path d="M2.5 1l3 3-3 3" fill="none" stroke="#8a9299" stroke-width="1.5"/></svg></span>
      </div>
    </div>
    <div class="card-grid">
      <article class="card"><div class="card-photo photo-b" role="img" aria-label="Photo of a new retail building"><span class="card-city">Surat</span></div><div class="card-body"><h4>Orvane Plaza</h4><p>Shopping Complex</p></div><a class="btn-view">View the listing</a></article>
      <article class="card"><div class="card-photo photo-a" role="img" aria-label="Photo of a new mall"><span class="card-city">Faridabad</span></div><div class="card-body"><h4>Orvane Plaza</h4><p>Shopping Complex</p></div><a class="btn-view">View the listing</a></article>
      <article class="card"><div class="card-photo photo-c" role="img" aria-label="Photo of a commercial tower"><span class="card-city">Gurgaon</span></div><div class="card-body"><h4>Orvane Plaza</h4><p>Shopping Complex</p></div><a class="btn-view">View the listing</a></article>
      <article class="card"><div class="card-photo photo-a" role="img" aria-label="Photo of a shopping centre"><span class="card-city">Noida</span></div><div class="card-body"><h4>Orvane Plaza</h4><p>Shopping Complex</p></div><a class="btn-view">View the listing</a></article>
      <article class="card"><div class="card-photo photo-b" role="img" aria-label="Photo of a glass tower"><span class="card-city">Gurgaon</span></div><div class="card-body"><h4>Orvane Plaza</h4><p>Shopping Complex</p></div><a class="btn-view">View the listing</a></article>
      <article class="card"><div class="card-photo photo-a" role="img" aria-label="Photo of twin retail towers"><span class="card-city">Surat</span></div><div class="card-body"><h4>Orvane Plaza</h4><p>Shopping Complex</p></div><a class="btn-view">View the listing</a></article>
      <article class="card"><div class="card-photo photo-c" role="img" aria-label="Photo of a mall at dusk"><span class="card-city">Faridabad</span></div><div class="card-body"><h4>Orvane Plaza</h4><p>Shopping Complex</p></div><a class="btn-view">View the listing</a></article>
      <article class="card"><div class="card-photo photo-b" role="img" aria-label="Photo of a retail block"><span class="card-city">Gurgaon</span></div><div class="card-body"><h4>Orvane Plaza</h4><p>Shopping Complex</p></div><a class="btn-view">View the listing</a></article>
      <article class="card"><div class="card-photo photo-a" role="img" aria-label="Photo of a shopping arcade"><span class="card-city">Noida</span></div><div class="card-body"><h4>Orvane Plaza</h4><p>Shopping Complex</p></div><a class="btn-view">View the listing</a></article>
      <article class="card"><div class="card-photo photo-b" role="img" aria-label="Photo of a high street building"><span class="card-city">Gurgaon</span></div><div class="card-body"><h4>Orvane Plaza</h4><p>Shopping Complex</p></div><a class="btn-view">View the listing</a></article>
    </div>
  </section>

  <footer class="site-footer">
    <div class="footer-cols">
      <div class="footer-col">
        <h5>EDITOR'S CHOICE</h5>
        <p>Hand-picked retail projects reviewed by our editors for location, footfall, design and value for retailers and investors this month.</p>
      </div>
      <div class="footer-col">
        <h5>ABOUT TRADEYARD RETAIL</h5>
        <ul class="footer-links">
          <li>About Us</li><li>Retail Malls</li>
          <li>Privacy Policy</li><li>High Street</li>
          <li>Terms of Use</li><li>Warehouses</li>
          <li>Contact Us</li><li>Advertise</li>
          <li>Site Map</li><li>Careers</li>
        </ul>
      </div>
      <div class="footer-col">
        <h5>CONTACT</h5>
        <p>Lotstallmart.com<br>Plot 14, Sector 44<br>Gurgaon, Haryana<br>Phone: +91 124 555 0182<br>hello@lotstallmart.com</p>
      </div>
      <div class="footer-col">
        <h5>FOLLOW US</h5>
        <ul class="follow-list">
          <li><i></i>Updates</li><li><i></i>News</li>
          <li><i></i>Network</li><li><i></i>Community</li>
        </ul>
      </div>
    </div>
    <div class="footer-brand"><span class="brand-dot"></span><span>lotstallmart</span></div>
  </footer>
  <div class="copyright">Copyright © 2015 Lotstallmart.com. All rights reserved.</div>

</div>
</body>
</html>
```